Halvern Studio Works New Business Card

I am opening a new division of my business. I am a high end interior designer, and the new business is writing specs for construction projects. It will be marketed to the VERY high end contractor, architects and realtors. The client will actually be the one who pays us and signs the agreement, but it will be the contractor, architect or realtor that will recommend us. I have attached my current card and our previous logo which is still used on some of our paperwork. I would like the new logo to be connected in some way to what we are currently using. We will need to have room on the card for a person's name. I'd like to omit the address as we might be moving the office soon. The web address is www.HalvernStudioWorks.com. For this design, please use my name, Marisol Thornbury.

Target Market(s)

High End Luxury Contractors, Realtors and Architects

Industry/Entity Type

Residential Construction

Contact Information for Business Card

Halvern Studio Works, Phone: 555-214-9087, www.HalvernStudioWorks.com , Marisol Thornbury

Font styles to use
Sans Serif

Colors
ec1f27

Requirements
Must have
• Some visual reference to my current card and logos. Use the colors submitted on the business card I attached.
Nice to have
• A visual reference to my current card and logos. Use the colors submitted on the card I attached.
Should not have
• A physical address

```html
<!DOCTYPE html>
<html lang="en">
<head>
<meta charset="utf-8">
<title>Halvern Studio Works — Business Card</title>
<link href="https://fonts.googleapis.com/css2?family=Raleway:wght@400&family=Source+Sans+3:wght@600;700&display=swap" rel="stylesheet">
<style>
  :root {
    --stage: #000000;
    --card: #ffffff;
    --card-back: #f7f7f7;
    --brand-red: #ec1f27;
    --ink-grey: #7a7a7a;
    --wordmark-grey: #808080;
    --deco-grey: #e6e6e8;
  }
  * { margin: 0; padding: 0; box-sizing: border-box; }
  html, body {
    width: 1200px; height: 1000px; overflow: hidden;
    background: var(--stage);
  }
  .canvas { position: relative; width: 1200px; height: 1000px; }

  .card { position: absolute; left: 259px; width: 682px; height: 390px; overflow: hidden; }

  /* Front */
  .card-front { top: 88px; background: var(--card); }
  .front-decor {
    position: absolute; inset: 0;
    background: radial-gradient(ellipse at 62% 55%, rgba(230,230,232,0.55) 0%, rgba(255,255,255,0) 70%);
  }
  .front-mark {
    position: absolute; left: 275px; top: 89px;
    width: 134px; height: 121px; background: var(--brand-red);
  }
  .front-name {
    position: absolute; left: 0; right: 0; top: 236px;
    text-align: center; padding-left: 20px;
    font-family: "Raleway", sans-serif; font-weight: 400;
    font-size: 40px; color: var(--wordmark-grey); letter-spacing: 0.5px;
  }

  /* Back */
  .card-back { top: 530px; height: 389px; background: var(--card-back); }
  .back-fold {
    position: absolute; left: 336px; top: 0; width: 10px; height: 100%;
    background: linear-gradient(to right, rgba(0,0,0,0.04), rgba(0,0,0,0.14) 45%, rgba(0,0,0,0.02));
  }
  .back-mark {
    position: absolute; left: 120px; top: 129px;
    width: 87px; height: 79px; background: var(--brand-red);
  }
  .back-name {
    position: absolute; left: 0; width: 340px; top: 222px;
    text-align: center;
    font-family: "Raleway", sans-serif; font-weight: 400;
    font-size: 24px; color: var(--wordmark-grey);
  }

  .contact {
    position: absolute; left: 387px; top: 118px;
    font-family: "Source Sans 3", sans-serif; font-weight: 600;
    color: var(--ink-grey);
  }
  .contact-name {
    font-weight: 700; font-size: 27px; line-height: 34px; color: var(--brand-red);
  }
  .contact-role { font-size: 17px; line-height: 22px; }
  .contact-lines { margin-top: 17px; font-size: 18px; line-height: 25px; }
  .contact-label { color: var(--brand-red); }
</style>
</head>
<body>
<main class="canvas">
  <section class="card card-front" aria-label="Card front">
    <div class="front-decor" role="img" aria-label="Faint large brand emblem in the background"></div>
    <div class="front-mark"></div>
    <p class="front-name">Halvern Studio Works</p>
  </section>

  <section class="card card-back" aria-label="Card back">
    <div class="back-mark"></div>
    <p class="back-name">Halvern Studio Works</p>
    <div class="back-fold"></div>
    <div class="contact">
      <p class="contact-name">Marisol Thornbury</p>
      <p class="contact-role">Professional Specifications<br>for Contractors</p>
      <div class="contact-lines">
        <p><span class="contact-label">Office:</span> 555.214.9087</p>
        <p><span class="contact-label">Cell:</span> 555.308.4172</p>
        <p>www.HalvernStudioWorks.com</p>
      </div>
    </div>
  </section>
</main>
</body>
</html>
```